Web design for Crowdfunding site HopeWingsRally.com

We need a web design for christian crowdfunding website. Here is the challenge: We need responsive layout that is targeted first in iPad size of screen. It should also scale somehow down to iPhone size of screens. Web layout can be about the same size as iPad screen.

Screens should work so that main page scrolls not but only certain part of the screen scrolls and always one "page" at time. We can implement these "scrolls" then later with javascript but now we need only design. The challenge is to create this kind of hybrid website / app look.

Target is at first to raise funds to orphan people needing about $40 per month for their living and education. There is always some organization which takes care of these kids. Later there will be other christian missions included. At first we are looking to find monthly supporters.

You can be as creative as you want :) As you see from the look and feel sector, I am not looking any same traditional look which many "help kids" sites have. I am looking to reach now younger generation and therefore iPad and mobile are the main screen sizes.

Inspirational designs:
- https://example-gallery.test/profiles/studiofernlake/designs/482716?from=%2Fbrowse%2Fxhr%2Fdesigns%3Fcategory%3Dmobile-app-design
- http://www.artpoolhub.test/design/8261047 Clear, simple visuals
- http://www.artpoolhub.test/design/7394215 Header
- http://www.artpoolhub.test/design/6048392 Contrast in the colors, i think is powerfull

Some terms could be: Kids play, kids are learning (in the school). No static posture but living like kids are. I wonder also how we could also add little bit gaming style even though the question is of reali life of real people. Giving should be rewarding.

Target Market(s)

People who want help other people.

Industry/Entity Type

Christian

Number of Pages Required

4 page

Requirements
Must have
• Homepage. Mission page (In my wireframes it was one kid).
Nice to have
• Other pages and some idea how to scroll. 4 pages is no must. If you feel easy, please give first some draft and I give comments on that.

```html
<!DOCTYPE html>
<html lang="en">
<head>
<meta charset="utf-8">
<title>HopeWingsRally – Mission: Orphan Maria</title>
<link rel="stylesheet" href="https://fonts.googleapis.com/css2?family=Montserrat:wght@400;500;600&family=Open+Sans:wght@400;600&display=swap">
<style>
  :root {
    --brand-yellow: #fdbf00;
    --ink: #1a1a1a;
    --panel: rgba(44, 44, 44, 0.92);
    --panel-line: rgba(255, 255, 255, 0.10);
    --row: #3a3a3a;
    --row-check: #6b6b6b;
    --text-light: #e6e6e6;
    --text-muted: #bdbdbd;
    --icon-grey: #a9a9a9;
  }
  * { box-sizing: border-box; margin: 0; padding: 0; }
  html, body { width: 1200px; height: 873px; overflow: hidden; background: #2a2a2a; }
  body { font-family: "Open Sans", Arial, sans-serif; color: var(--text-light); }

  .page { position: relative; width: 1200px; height: 873px; overflow: hidden; }
  .page-backdrop {
    position: absolute; inset: 0;
    background: radial-gradient(ellipse at 60% 40%, #575757 0%, #3a3a3a 45%, #242424 100%);
  }

  /* Header */
  .site-header {
    position: absolute; left: 0; top: 0; width: 1200px; height: 84px;
    background: var(--brand-yellow); color: var(--ink);
    font-family: "Montserrat", Arial, sans-serif;
  }
  .menu-link { position: absolute; left: 12px; top: 28px; display: flex; align-items: center; gap: 12px; font-size: 22px; font-weight: 500; }
  .search-btn { position: absolute; left: 277px; top: 17px; width: 48px; height: 45px; border: 2px solid var(--ink); border-radius: 3px; display: flex; align-items: center; justify-content: center; }
  .brand-name { position: absolute; left: 0; right: 0; top: 14px; text-align: center; font-size: 46px; font-weight: 400; letter-spacing: 0.5px; }
  .auth-btn { position: absolute; top: 17px; height: 45px; border: 2px solid var(--ink); border-radius: 3px; font-size: 19px; font-weight: 500; display: flex; align-items: center; justify-content: center; }
  .auth-btn.login { left: 968px; width: 105px; }
  .auth-btn.signup { left: 1085px; width: 105px; }

  /* Scroll indicator */
  .scroll-rail { position: absolute; left: 14px; top: 127px; width: 3px; height: 746px; background: rgba(255,255,255,0.35); }
  .scroll-rail .thumb { position: absolute; left: 0; top: 0; width: 6px; height: 8px; background: #fff; }
  .scroll-rail .marker { position: absolute; left: 0; top: 480px; width: 8px; height: 6px; background: var(--brand-yellow); }

  /* Title */
  .mission-title { position: absolute; left: 37px; top: 123px; font-family: "Montserrat", Arial, sans-serif; font-size: 35px; font-weight: 500; color: #fff; }
  .share-links { position: absolute; right: 10px; top: 132px; display: flex; gap: 22px; align-items: center; }
  .share-links span { display: block; width: 26px; height: 26px; border-radius: 50%; background: var(--icon-grey); }

  /* Story column */
  .story { position: absolute; left: 36px; top: 181px; width: 752px; height: 692px; overflow: hidden; }
  .tabs { display: flex; border-top: 4px solid var(--brand-yellow); height: 56px; font-family: "Montserrat", Arial, sans-serif; font-size: 24px; }
  .tab { padding: 10px 0 0; width: 137px; text-align: center; color: #eee; }
  .tab.active { background: var(--brand-yellow); color: var(--ink); }
  .tab.updates { width: 180px; }
  .tab.comments { width: 170px; }
  .story-text { font-size: 15px; line-height: 27.5px; color: #e9e9e9; margin-top: 26px; }
  .story-text + .story-text { margin-top: 27px; }
  .story-photo { margin-top: 33px; width: 752px; height: 231px; background: linear-gradient(90deg, #6f7aa0 0%, #c97c55 45%, #e35a2a 65%, #8a86a8 100%); }
  .story-photo + .story-text { margin-top: 44px; }

  /* Sidebar */
  .sidebar { position: absolute; left: 1012px; top: 178px; width: 368px; margin-left: -188px; height: 695px; background: var(--panel); border: 1px solid var(--panel-line); overflow: hidden; }
  .kid-card { height: 130px; padding: 20px 20px 0; border-bottom: 1px solid var(--panel-line); }
  .kid-name { font-family: "Montserrat", Arial, sans-serif; font-size: 25px; font-weight: 500; color: #fff; }
  .kid-meta { margin-top: 10px; font-size: 14px; line-height: 22px; color: var(--text-muted); }
  .kid-meta svg { vertical-align: -2px; margin-right: 6px; }
  .supporters { height: 65px; padding: 0 20px; display: flex; align-items: center; border-bottom: 1px solid var(--panel-line); font-size: 15px; color: var(--text-muted); }
  .supporters .label { margin-right: 16px; }
  .avatar { width: 35px; height: 35px; border-radius: 50%; background: linear-gradient(#c79a7d, #7c5a48); border: 2px solid #fff; margin-right: 11px; }
  .supporters .more { margin-left: 8px; }
  .my-support { height: 183px; padding: 22px 20px 0; border-bottom: 1px solid var(--panel-line); }
  .my-support .heading { font-size: 17px; color: var(--brand-yellow); display: flex; align-items: center; gap: 10px; }
  .progress { display: flex; align-items: center; margin-top: 16px; }
  .progress-ring { position: relative; width: 92px; height: 92px; }
  .progress-ring .value { position: absolute; inset: 0; display: flex; align-items: center; justify-content: center; font-family: "Montserrat", Arial, sans-serif; font-size: 24px; font-weight: 600; color: #fff; }
  .progress-ring .value small { font-size: 12px; margin-top: -8px; }
  .progress-facts { margin-left: 20px; }
  .progress-facts .given { font-size: 18px; color: #fff; }
  .progress-facts .total { font-size: 14px; color: var(--text-muted); margin-top: 1px; }
  .progress-facts .need { font-size: 17px; color: #fff; margin-top: 10px; display: flex; align-items: center; gap: 10px; }
  .participate-title { padding: 28px 20px 0; font-size: 18px; color: var(--brand-yellow); }
  .options { list-style: none; margin-top: 8px; padding: 0 3px; }
  .option { height: 61px; margin-bottom: 5px; background: var(--row); display: flex; align-items: center; padding: 0 18px 0 22px; font-size: 17px; color: #ddd; }
  .option .check { width: 37px; height: 37px; background: var(--row-check); border-radius: 3px; margin-right: 22px; }
  .option .label { flex: 1; }
</style>
</head>
<body>
<div class="page">
  <div class="page-backdrop" role="img" aria-label="Darkened photo of many hands joined together"></div>

  <header class="site-header">
    <div class="menu-link">
      <svg width="18" height="16" viewBox="0 0 18 16"><rect y="1" width="18" height="3" fill="#1a1a1a"/><rect y="7" width="18" height="3" fill="#1a1a1a"/><rect y="13" width="18" height="3" fill="#1a1a1a"/></svg>
      See the missions
    </div>
    <div class="search-btn">
      <svg width="22" height="22" viewBox="0 0 22 22"><circle cx="9" cy="9" r="6.5" fill="none" stroke="#1a1a1a" stroke-width="3"/><line x1="14" y1="14" x2="20" y2="20" stroke="#1a1a1a" stroke-width="3.5" stroke-linecap="round"/></svg>
    </div>
    <div class="brand-name">HopeWingsRally</div>
    <div class="auth-btn login">Log In</div>
    <div class="auth-btn signup">Sign Up</div>
  </header>

  <div class="scroll-rail"><span class="thumb"></span><span class="marker"></span></div>

  <h1 class="mission-title">Mission : Orphan Maria, 11y</h1>
  <div class="share-links" aria-label="Share"><span></span><span></span><span></span><span></span></div>

  <section class="story">
    <nav class="tabs">
      <div class="tab active">Story</div>
      <div class="tab updates">Updates</div>
      <div class="tab comments">Comments</div>
    </nav>
    <p class="story-text">Aenean fermentum felis sem, a elementum erat aliquet sed. In purus mauris, rutrum et eros vel, elementum laoreet ipsum. Sed a placerat dui. Suspendisse ac lectus eget augue pulvinar placerat id sed mi. Class aptent taciti sociosqu ad litora torquent per conubia nostra, per inceptos himenaeos. Donec tempor lorem in massa varius, ac hendrerit diam imperdiet. Ut sit amet blandit arcu. Cras ut consectetur ante. Phasellus hendrerit, ipsum a mollis sollicitudin, elit tellus ornare dui.</p>
    <p class="story-text">Donec eu neque id mauris sodales faucibus non eget nisi. Quisque facilisis id nunc porttitor imperdiet. Suspendisse volutpat vel orci fringilla mattis. Pellentesque ut blandit augue.</p>
    <div class="story-photo" role="img" aria-label="Girl silhouetted against a sunset sky holding red balloons"></div>
    <p class="story-text">Aenean fermentum felis sem, a elementum erat aliquet sed. In purus mauris, rutrum et eros vel, elementum laoreet ipsum. Sed a placerat dui. Suspendisse ac lectus eget augue pulvinar placerat id sed mi. Class aptent taciti sociosqu ad litora torquent per conubia nostra, per inceptos himenaeos. Donec tempor lorem in massa varius, ac hendrerit diam imperdiet. Donec eu neque id mauris sodales faucibus non eget nisi.</p>
  </section>

  <aside class="sidebar">
    <div class="kid-card">
      <div class="kid-name">Name : Maria, 11y</div>
      <div class="kid-meta">
        <div><svg width="9" height="13" viewBox="0 0 9 13"><path d="M4.5 0A4.5 4.5 0 0 0 0 4.5C0 8 4.5 13 4.5 13S9 8 9 4.5A4.5 4.5 0 0 0 4.5 0z" fill="#bdbdbd"/><circle cx="4.5" cy="4.5" r="1.6" fill="#2c2c2c"/></svg>Kalkutta</div>
        <div>Organization : Jacob</div>
      </div>
    </div>
    <div class="supporters">
      <span class="label">Support</span>
      <span class="avatar" role="img" aria-label="Supporter portrait"></span>
      <span class="avatar" role="img" aria-label="Supporter portrait"></span>
      <span class="avatar" role="img" aria-label="Supporter portrait"></span>
      <span class="avatar" role="img" aria-label="Supporter portrait"></span>
      <span class="avatar" role="img" aria-label="Supporter portrait"></span>
      <svg class="more" width="9" height="14" viewBox="0 0 9 14"><path d="M1.5 1.5 7 7l-5.5 5.5" fill="none" stroke="#bdbdbd" stroke-width="2"/></svg>
    </div>
    <div class="my-support">
      <div class="heading">My Support is now : $5 / month
        <svg width="10" height="10" viewBox="0 0 10 10"><path d="M1 1l8 8M9 1 1 9" stroke="#bdbdbd" stroke-width="2.5"/></svg>
      </div>
      <div class="progress">
        <div class="progress-ring">
          <svg width="92" height="92" viewBox="0 0 92 92">
            <circle cx="46" cy="46" r="40" fill="none" stroke="#9a9a9a" stroke-width="8"/>
            <circle cx="46" cy="46" r="40" fill="none" stroke="#fdbf00" stroke-width="8" stroke-dasharray="113.1 251.3" transform="rotate(-90 46 46)"/>
          </svg>
          <div class="value">45<small>%</small></div>
        </div>
        <div class="progress-facts">
          <div class="given">$15 given</div>
          <div class="total">of total $35 needed</div>
          <div class="need">
            <svg width="16" height="16" viewBox="0 0 16 16"><rect x="1" y="2.5" width="14" height="12.5" fill="none" stroke="#bdbdbd" stroke-width="1.5"/><line x1="1" y1="6" x2="15" y2="6" stroke="#bdbdbd" stroke-width="1.5"/><path d="M4 9h2M7 9h2M10 9h2M4 12h2M7 12h2M10 12h2" stroke="#bdbdbd" stroke-width="1.5"/></svg>
            per month need
          </div>
        </div>
      </div>
    </div>
    <div class="participate-title">Participate</div>
    <ul class="options">
      <li class="option"><span class="check"></span><span class="label">I am in, $1 / month</span><svg width="20" height="18" viewBox="0 0 20 18"><path d="M0 1h3.5l2.5 10h11l2-7H5" fill="none" stroke="#bdbdbd" stroke-width="2"/><path d="M5 4h14l-2 7H6z" fill="#bdbdbd"/><circle cx="7.5" cy="15" r="1.8" fill="#bdbdbd"/><circle cx="15.5" cy="15" r="1.8" fill="#bdbdbd"/></svg></li>
      <li class="option"><span class="check"></span><span class="label">Increased, $5 / month</span><svg width="20" height="18" viewBox="0 0 20 18"><path d="M0 1h3.5l2.5 10h11l2-7H5" fill="none" stroke="#bdbdbd" stroke-width="2"/><path d="M5 4h14l-2 7H6z" fill="#bdbdbd"/><circle cx="7.5" cy="15" r="1.8" fill="#bdbdbd"/><circle cx="15.5" cy="15" r="1.8" fill="#bdbdbd"/></svg></li>
      <li class="option"><span class="check"></span><span class="label">Decent help, $10 / month</span><svg width="20" height="18" viewBox="0 0 20 18"><path d="M0 1h3.5l2.5 10h11l2-7H5" fill="none" stroke="#bdbdbd" stroke-width="2"/><path d="M5 4h14l-2 7H6z" fill="#bdbdbd"/><circle cx="7.5" cy="15" r="1.8" fill="#bdbdbd"/><circle cx="15.5" cy="15" r="1.8" fill="#bdbdbd"/></svg></li>
      <li class="option"><span class="check"></span><span class="label">Whole kid, $35 / month</span><svg width="20" height="18" viewBox="0 0 20 18"><path d="M0 1h3.5l2.5 10h11l2-7H5" fill="none" stroke="#bdbdbd" stroke-width="2"/><path d="M5 4h14l-2 7H6z" fill="#bdbdbd"/><circle cx="7.5" cy="15" r="1.8" fill="#bdbdbd"/><circle cx="15.5" cy="15" r="1.8" fill="#bdbdbd"/></svg></li>
    </ul>
  </aside>
</div>
</body>
</html>
```